Business Cards used to invite people to our church

We are a church and have need of a business card sized advertisement that allows our members to hand them out in order to invite people to the church. I need the front of the card to say "You're Invited" or "Come Check us out". with the service times on the back of the card later.
I have attached one of the OLD cards we have used in the past, but we want a complete makeover, into a more modern style that does not require the image.
I am also replacing the old logo with a newer "flat" logo which is attached.
Please use marketing colors. (blue or red or something that catches attention)
Create a card that DOES NOT have the picture of the two people on the front
The information on the sample card back is correct to go onto new card
Target Market(s)
anyone
Industry/Entity Type
Business
Contact Information for Business Card
sertice times and address information which you can get from the sample card I uploaded. It should have "You're Invited" or "Come Check us out" on the front of the card with out logo.

```html
<!DOCTYPE html>
<html lang="en">
<head>
<meta charset="utf-8">
<title>Harbor Light Ministries – Invitation Card</title>
<link rel="stylesheet" href="https://fonts.googleapis.com/css2?family=Open+Sans:wght@400;600;700&display=swap">
<style>
  :root {
    --backdrop: #2b2b2d;
    --card-red: #ff0a0a;
    --card-red-deep: #e80000;
    --ink-white: #ffffff;
    --ink-soft: rgba(255,255,255,0.9);
  }
  * { box-sizing: border-box; margin: 0; padding: 0; }
  html, body {
    width: 1200px; height: 900px; overflow: hidden;
    background: var(--backdrop);
    font-family: "Open Sans", Arial, sans-serif;
  }
  .sheet {
    width: 1200px; height: 900px;
    display: flex; align-items: center; justify-content: center; gap: 60px;
  }
  .card {
    position: relative;
    width: 520px; height: 330px;
    border-radius: 22px;
    background: var(--card-red);
    color: var(--ink-white);
    overflow: hidden;
  }
  /* Front */
  .card-front .invite-line {
    position: absolute; left: 0; right: 0; top: 150px;
    font-weight: 700; font-size: 40px; letter-spacing: 0.5px;
  }
  .invite-word { position: absolute; }
  .word-come  { left: 28px;  top: 24px; }
  .word-check { left: 170px; top: 6px; }
  .word-us    { left: 322px; top: 2px; }
  .word-out   { left: 410px; top: 14px; }

  /* Back */
  .card-back { padding: 34px 40px 28px; }
  .brand {
    display: flex; align-items: center; justify-content: center; gap: 10px;
    font-weight: 600; font-size: 22px; letter-spacing: 1.5px; text-transform: uppercase;
  }
  .brand-mark { width: 18px; height: 18px; background: var(--ink-white); }
  .schedule { margin: 34px auto 0; width: 340px; list-style: none; font-size: 15px; }
  .schedule li { display: flex; align-items: baseline; line-height: 26px; }
  .schedule .leader {
    flex: 1; margin: 0 4px;
    border-bottom: 2px dotted var(--ink-soft); transform: translateY(-4px);
  }
  .contact { margin: 14px auto 0; width: 340px; font-size: 14px; text-align: right; }
  .contact-line { display: flex; align-items: center; justify-content: flex-end; gap: 6px; }
  .address { margin-top: 12px; justify-content: center; font-weight: 700; font-size: 14px; }
  .contact svg { fill: var(--ink-white); }
</style>
</head>
<body>
<main class="sheet">
  <section class="card card-front" aria-label="Card front">
    <p class="invite-line">
      <span class="invite-word word-come">Come</span>
      <span class="invite-word word-check">Check</span>
      <span class="invite-word word-us">us</span>
      <span class="invite-word word-out">out</span>
    </p>
  </section>

  <section class="card card-back" aria-label="Card back">
    <div class="brand"><span class="brand-mark"></span>Harbor Light Ministries</div>
    <ul class="schedule">
      <li><span>Sunday</span><span class="leader"></span><span>9:00 Am</span></li>
      <li><span>Sunday</span><span class="leader"></span><span>11:00 Am</span></li>
      <li><span>Wed. Bible Class</span><span class="leader"></span><span>7:00 Pm</span></li>
    </ul>
    <div class="contact">
      <p class="contact-line">
        <svg width="13" height="13" viewBox="0 0 24 24" aria-hidden="true"><path d="M6.6 10.8a15 15 0 0 0 6.6 6.6l2.2-2.2c.3-.3.7-.4 1-.2 1.1.4 2.3.6 3.6.6.6 0 1 .4 1 1V20c0 .6-.4 1-1 1A17 17 0 0 1 3 4c0-.6.4-1 1-1h3.5c.6 0 1 .4 1 1 0 1.3.2 2.5.6 3.6.1.3 0 .7-.2 1z"/></svg>
        1-800-555-0142
      </p>
      <p class="contact-line address">
        <svg width="11" height="14" viewBox="0 0 24 30" aria-hidden="true"><path d="M12 0C5.4 0 0 5.4 0 12c0 9 12 18 12 18s12-9 12-18C24 5.4 18.6 0 12 0zm0 17a5 5 0 1 1 0-10 5 5 0 0 1 0 10z"/></svg>
        2480, Cedar Lane - Maplewood, Tx 75099
      </p>
    </div>
  </section>
</main>
</body>
</html>
```